Redesign This Psychology Website

We would like a slight redesign of this successful psychology (relationship counselling) website:

www.TheKelvaleClinic.com.au

We are updating the website, and we'd like a slight refresh of the design and style.

Please keep to very similar colours, and use the same logo. We're looking for around 10 page templates, however the main one is the home page.

Keep in mind, this website already converts quite well, so we want a new, fresh design in keeping with this one. Please don't bother designing something too extremely different.

thanks :)

Target Market(s)

couples who are looking for relationship counselling. Men and women, 25 - 70, across Australia

Industry/Entity Type

Psychology

Number of Pages Required

5+ page

Font styles to use
Sans Serif

Colors
87cfc6
b7a5cd
ec1f27
ffffff
cee9f5

Requirements
Must have
• a similar look to the current design, just looking for a slight refresh.
• Search bar
• Areas for lots of photos
• same logo
• lots of content areas
Nice to have
• great content areas, where we can display a lot of content and our areas.
Should not have
• no colors like orange, etc.
• should not have a totally different feel.

```html
<!DOCTYPE html>
<html lang="en">
<head>
<meta charset="utf-8">
<title>The Kelvale Clinic – Relationship &amp; Marriage Counselling</title>
<link href="https://fonts.googleapis.com/css2?family=Open+Sans:wght@300;400;600;700&display=swap" rel="stylesheet">
<style>
:root{
  --teal:#87cfc6;
  --teal-dark:#4fb3a8;
  --purple:#b7a5cd;
  --purple-dark:#9a86b8;
  --red:#ec1f27;
  --white:#ffffff;
  --sky:#cee9f5;
  --ink:#3d3d3d;
  --muted:#8a8a8a;
  --line:#e4e4e4;
  --paper:#f3f3f3;
}
*{box-sizing:border-box;margin:0;padding:0}
html,body{width:1200px;height:3972px;overflow:hidden}
body{font-family:"Open Sans",Arial,sans-serif;color:var(--ink);background:var(--white);font-size:14px;line-height:1.5}
.wrap{width:1080px;margin:0 auto;position:relative}
a{color:inherit;text-decoration:none}

/* top strip */
.top-strip{height:28px;background:var(--paper);border-bottom:1px solid var(--line);font-size:11px;color:var(--muted)}
.top-strip .wrap{display:flex;justify-content:space-between;align-items:center;height:28px}
.top-links{display:flex;gap:18px}

/* header */
.site-header{height:122px}
.site-header .wrap{display:flex;align-items:center;justify-content:space-between;height:122px}
.brand{display:flex;align-items:center;gap:12px}
.brand-dot{width:46px;height:46px;border-radius:50%;background:var(--teal)}
.brand-name{font-size:30px;font-weight:600;color:var(--teal-dark);line-height:1}
.brand-tag{font-size:11px;color:var(--muted);margin-top:4px}
.search-box{width:300px;height:36px;border:1px solid var(--line);border-radius:3px;display:flex;align-items:center;padding:0 12px;gap:8px;color:var(--muted);font-size:12px;margin-left:-120px}
.call{text-align:right}
.call small{display:block;font-size:12px;color:var(--muted)}
.call strong{font-size:28px;color:var(--red);font-weight:700;line-height:1.1}

/* nav */
.main-nav{height:80px;background:linear-gradient(180deg,var(--teal),var(--teal-dark))}
.main-nav ul{list-style:none;display:flex;height:80px;align-items:center}
.main-nav li{color:var(--white);font-size:13px;font-weight:600;text-transform:uppercase;padding:0 22px;border-right:1px solid rgba(255,255,255,.35);line-height:1.25;max-width:230px}
.main-nav li:last-child{border-right:0}

/* hero */
.hero{height:522px;position:relative;background:linear-gradient(120deg,#7e9a5a 0%,#c7d4a0 30%,#e9e3cf 55%,#8aa866 80%,#5e7d3e 100%)}
.hero-title{position:absolute;left:60px;top:268px;color:var(--white);font-size:40px;font-weight:600;text-transform:uppercase;line-height:1.15;text-shadow:0 2px 6px rgba(0,0,0,.25)}
.finder{position:absolute;left:768px;top:120px;width:320px;padding:24px 26px;background:rgba(183,165,205,.94);border-radius:4px;color:var(--white)}
.finder h2{font-size:22px;font-weight:600;line-height:1.2;margin-bottom:14px}
.finder label{display:block;font-size:12px;margin:10px 0 4px}
.finder .field{height:32px;background:var(--white);border-radius:2px;color:var(--muted);font-size:12px;padding:6px 10px;display:flex;justify-content:space-between}
.finder .go{margin-top:16px;height:38px;background:var(--red);border-radius:2px;text-align:center;line-height:38px;font-weight:700;font-size:14px}
.dots{display:flex;gap:8px;justify-content:center}
.dots span{width:9px;height:9px;border-radius:50%;background:rgba(255,255,255,.6)}
.dots span.on{background:var(--white)}
.hero .dots{position:absolute;bottom:20px;left:0;right:0}

/* intro */
.intro{height:418px;padding-top:60px}
.intro .wrap{display:flex;gap:48px}
.video{width:440px;height:290px;background:linear-gradient(135deg,#d9d4cd,#a9a39c);position:relative;flex:none}
.play{position:absolute;left:50%;top:50%;width:64px;height:64px;margin:-32px 0 0 -32px;border-radius:50%;background:rgba(255,255,255,.85)}
.intro h2{font-size:30px;font-weight:600;color:var(--ink);line-height:1.25;margin:20px 0 16px}
.intro p{font-size:14px;color:var(--muted);line-height:1.75}
.notch{width:0;height:0;margin:0 auto;border-left:18px solid transparent;border-right:18px solid transparent;border-top:16px solid var(--line)}

/* services */
.services{height:420px;padding-top:24px}
.services .wrap{display:flex;gap:20px}
.svc{flex:1;border:1px solid var(--line);background:var(--white)}
.svc-img{height:170px}
.svc-body{padding:16px 16px 20px}
.svc h3{font-size:17px;color:var(--teal-dark);font-weight:600;line-height:1.25;margin-bottom:8px}
.svc p{font-size:12px;color:var(--muted);line-height:1.6;margin-bottom:12px}
.btn{display:inline-block;padding:7px 16px;font-size:12px;font-weight:600;color:var(--white);border-radius:2px}
.btn-purple{background:var(--purple)}
.btn-red{background:var(--red)}
.btn-teal{background:var(--teal-dark)}

/* psychologists band */
.team{height:440px;position:relative;overflow:hidden;background:var(--white)}
.team-photo{position:absolute;right:0;top:0;width:640px;height:440px;background:linear-gradient(135deg,#9fb8cc,#d8cfc6 50%,#b89c85)}
.team-panel{position:absolute;inset:0}
.team-copy{position:absolute;left:60px;top:52px;width:620px;color:var(--white)}
.team-copy h2{font-size:32px;font-weight:300;margin-bottom:4px}
.team-copy .lead{font-size:13px;opacity:.9;margin-bottom:22px}
.issues{display:grid;grid-template-columns:1fr 1fr;column-gap:40px;row-gap:8px;list-style:none;font-size:13px}
.issues li{display:flex;align-items:center;gap:8px}

/* two-col copy */
.patterns{height:380px;padding-top:60px}
.patterns .wrap{display:flex;gap:60px}
.patterns article{flex:1}
.patterns h2{font-size:28px;font-weight:400;line-height:1.25;margin-bottom:16px}
.h-red{color:var(--red)}
.h-teal{color:var(--teal-dark)}
.patterns p{font-size:13px;color:var(--muted);line-height:1.75;margin-bottom:20px}

/* topics */
.topics{height:400px;background:var(--paper);padding-top:40px}
.topics .row{display:flex;gap:20px}
.topic{flex:1;height:270px;position:relative}
.topic span{position:absolute;left:0;right:0;bottom:0;height:44px;line-height:44px;padding-left:18px;background:rgba(79,179,168,.92);color:var(--white);font-weight:600;font-size:15px}
.topics .dots{margin-top:24px}
.topics .dots span{background:#cfcfcf;width:26px;height:4px;border-radius:2px}
.topics .dots span.on{background:var(--teal-dark)}

/* blogs */
.blogs{height:780px;padding-top:56px}
.blogs h2{font-size:34px;font-weight:600;color:var(--ink);margin-bottom:28px}
.blog-grid{display:grid;grid-template-columns:repeat(4,1fr);column-gap:24px;row-gap:40px}
.post-img{height:180px;position:relative}
.date{position:absolute;left:12px;top:12px;width:48px;height:52px;background:var(--teal-dark);color:var(--white);text-align:center;font-size:11px;line-height:1.2;padding-top:8px}
.date b{display:block;font-size:18px}
.post h3{font-size:15px;font-weight:600;margin:12px 0 6px}
.post p{font-size:12px;color:var(--muted);line-height:1.6;margin-bottom:6px}
.post .more{font-size:12px;color:var(--teal-dark);font-weight:600}

/* footer */
.site-footer{height:292px;border-top:1px solid var(--line);padding-top:48px}
.site-footer .wrap{display:flex;justify-content:space-between}
.footer-brand{width:340px}
.foot-col{width:200px}
.foot-col h4{font-size:14px;font-weight:700;color:var(--teal-dark);margin-bottom:12px;text-transform:uppercase}
.foot-col li{list-style:none;font-size:12px;color:var(--muted);line-height:2}
.social{display:flex;gap:8px;margin-top:10px}
.social span{width:28px;height:28px;border-radius:50%;background:var(--teal-dark)}
.bottom-bar{height:72px;background:var(--paper);text-align:center;line-height:72px;font-size:12px;color:var(--muted)}
</style>
</head>
<body>

<div class="top-strip">
  <div class="wrap">
    <span>Join Our Associates Program ›</span>
    <nav class="top-links"><a>Home</a><a>Care</a><a>Blog</a><a>Resources</a><a>Contact</a></nav>
  </div>
</div>

<header class="site-header">
  <div class="wrap">
    <div class="brand">
      <span class="brand-dot"></span>
      <div>
        <div class="brand-name">The Kelvale Clinic</div>
        <div class="brand-tag">helping you create loving relationships</div>
      </div>
    </div>
    <div class="search-box">
      <svg width="14" height="14" viewBox="0 0 14 14"><circle cx="6" cy="6" r="4.5" fill="none" stroke="#8a8a8a" stroke-width="1.5"/><line x1="9.5" y1="9.5" x2="13" y2="13" stroke="#8a8a8a" stroke-width="1.5"/></svg>
      Search Here
    </div>
    <div class="call"><small>Call Us Now</small><strong>1300 555 014</strong></div>
  </div>
</header>

<nav class="main-nav">
  <ul class="wrap">
    <li>Counselling<br>Types</li>
    <li>Relationship Counselling<br>Locations</li>
    <li>Sex Therapy<br>Locations</li>
    <li>About Us</li>
    <li>Quizzes</li>
    <li>FAQ's</li>
    <li>Contact</li>
  </ul>
</nav>

<section class="hero">
  <div role="img" aria-label="Smiling couple embracing outdoors in a sunny park" style="position:absolute;inset:0"></div>
  <h1 class="hero-title">Relationship &amp;<br>Marriage Counselling</h1>
  <form class="finder">
    <h2>Find Our Psychologist<br>Near You</h2>
    <label>Type of Counselling</label>
    <div class="field"><span>Select</span><span>▾</span></div>
    <label>Location</label>
    <div class="field"><span>Enter suburb</span></div>
    <label>Postcode</label>
    <div class="field"><span>Enter postcode</span></div>
    <div class="go">SEARCH</div>
  </form>
  <div class="dots"><span class="on"></span><span></span><span></span><span></span></div>
</section>

<section class="intro">
  <div class="wrap">
    <div class="video" role="img" aria-label="Video still of a counsellor speaking to camera"><span class="play"></span></div>
    <div>
      <h2>We Specialise in Relationship<br>&amp; Marriage Counselling</h2>
      <p>At The Kelvale Clinic, we are a group of psychologists across Australia who are passionate about relationships and helping you with yours. Our vision is to provide the most highly regarded and comprehensive marriage counselling and relationship counselling service in Australia, one that is caring, practical, accessible and affordable for every couple we work with.</p>
    </div>
  </div>
</section>
<div class="notch"></div>

<section class="services">
  <div class="wrap">
    <article class="svc">
      <div class="svc-img" role="img" aria-label="Couple talking with a counsellor" style="background:linear-gradient(135deg,#d8d2ca,#a89f96)"></div>
      <div class="svc-body"><h3>Relationship<br>Counselling</h3><p>Practical support to help couples reconnect, communicate and grow together.</p><a class="btn btn-purple">Learn More</a></div>
    </article>
    <article class="svc">
      <div class="svc-img" role="img" aria-label="Couple resting together in bed" style="background:linear-gradient(135deg,#e6dcd2,#c2aa98)"></div>
      <div class="svc-body"><h3>Sex Therapy<br>Counselling</h3><p>Confidential help to rebuild intimacy, trust and closeness with your partner.</p><a class="btn btn-purple">Learn More</a></div>
    </article>
    <article class="svc">
      <div class="svc-img" role="img" aria-label="Couple in a tense discussion" style="background:linear-gradient(135deg,#cfc7bf,#8f857c)"></div>
      <div class="svc-body"><h3>Anger Management<br>Counselling</h3><p>Learn calmer ways to handle conflict and express difficult feelings safely.</p><a class="btn btn-purple">Learn More</a></div>
    </article>
    <article class="svc">
      <div class="svc-img" role="img" aria-label="Man looking away from his partner" style="background:linear-gradient(135deg,#b9ab9e,#6f6358)"></div>
      <div class="svc-body"><h3>Narcissism<br>Counselling</h3><p>Guidance for partners living with controlling or self-centred behaviour.</p><a class="btn btn-purple">Learn More</a></div>
    </article>
  </div>
</section>

<section class="team">
  <div class="team-photo" role="img" aria-label="Smiling mature couple embracing"></div>
  <svg class="team-panel" width="1200" height="440" viewBox="0 0 1200 440" aria-hidden="true">
    <defs><linearGradient id="bandFade" x1="0" y1="0" x2="1" y2="0"><stop offset="0" stop-color="#b7a5cd"/><stop offset="1" stop-color="#cbbddc" stop-opacity=".85"/></linearGradient></defs>
    <polygon points="0,0 820,0 680,440 0,440" fill="url(#bandFade)"/>
  </svg>
  <div class="team-copy">
    <h2>Our Kelvale Relationship Psychologists</h2>
    <p class="lead">Here are some of the common areas we help with:</p>
    <ul class="issues">
      <li>✓ Affairs</li><li>✓ Relationship neglect</li>
      <li>✓ Controlling behaviour</li><li>✓ Sexual problems</li>
      <li>✓ Verbal abuse</li><li>✓ Problems from childhood</li>
      <li>✓ Imbalance of power</li><li>✓ Problems with parenting your children</li>
      <li>✓ Lack of intimacy</li><li>✓ New children and in-laws</li>
      <li>✓ Poor communication</li><li>✓ All forms of family problems</li>
      <li>✓ Loss of trust</li><li>✓ Anger management problems</li>
    </ul>
  </div>
</section>

<section class="patterns">
  <div class="wrap">
    <article>
      <h2 class="h-red">Communication is a vital skill<br>but not often taught to us.</h2>
      <p>Most people find that their ways of communicating with each other are shaped by what they saw growing up. Effective interpersonal communication skills are rarely taught at school, so many couples struggle to share feelings, resolve disagreements and feel truly heard by one another.</p>
      <a class="btn btn-red">Learn More</a>
    </article>
    <article>
      <h2 class="h-teal">We as individuals have specific<br>patterns in our relationships.</h2>
      <p>We can also assist you if you want individual help and guidance in your relationship. Together we can look at the patterns you bring into your relationships, why they repeat, and how you can build healthier connections that meet your needs.</p>
      <a class="btn btn-teal">Learn More</a>
    </article>
  </div>
</section>

<section class="topics">
  <div class="wrap">
    <div class="row">
      <div class="topic" role="img" aria-label="Woman sitting alone looking upset" style="background:linear-gradient(135deg,#a69a8e,#5e544b)"><span>How to Deal with an Affair?</span></div>
      <div class="topic" role="img" aria-label="Two men sharing a quiet moment" style="background:linear-gradient(135deg,#c9bba9,#7c6d5d)"><span>Same Sex Relationship</span></div>
      <div class="topic" role="img" aria-label="Couple arguing in a dim room" style="background:linear-gradient(135deg,#8a7f76,#3e3832)"><span>Are You living with a narcissist?</span></div>
    </div>
    <div class="dots"><span class="on"></span><span></span><span></span></div>
  </div>
</section>

<section class="blogs">
  <div class="wrap">
    <h2>Latest Blogs</h2>
    <div class="blog-grid">
      <article class="post"><div class="post-img" role="img" aria-label="Couple holding hands" style="background:linear-gradient(135deg,#e2d4c6,#b69b85)"><span class="date"><b>12</b>JUN</span></div><h3>Your Blog Title here</h3><p>Simple ways to rebuild trust after a hard season, and small steps to start today.</p><a class="more">Read More</a></article>
      <article class="post"><div class="post-img" role="img" aria-label="Couple talking on a sofa" style="background:linear-gradient(135deg,#d5ccc3,#9a8b7d)"><span class="date"><b>08</b>JUN</span></div><h3>Your Blog Title here</h3><p>What healthy conflict looks like and why it can bring partners closer together.</p><a class="more">Read More</a></article>
      <article class="post"><div class="post-img" role="img" aria-label="Couple sharing a kiss" style="background:linear-gradient(135deg,#dccfc8,#a88f83)"><span class="date"><b>02</b>JUN</span></div><h3>Your Blog Title here</h3><p>Keeping romance alive when work, children and daily routines take over.</p><a class="more">Read More</a></article>
      <article class="post"><div class="post-img" role="img" aria-label="Group of friends laughing together" style="background:linear-gradient(135deg,#cfd6db,#8a979f)"><span class="date"><b>27</b>MAY</span></div><h3>Your Blog Title here</h3><p>How friendships and family support shape the health of your relationship.</p><a class="more">Read More</a></article>
      <article class="post"><div class="post-img" role="img" aria-label="Man and woman in a serious conversation" style="background:linear-gradient(135deg,#c4bab1,#786b60)"></div><h3>Your Blog Title here</h3><p>Recognising the early signs of drifting apart and what you can do about it.</p><a class="more">Read More</a></article>
      <article class="post"><div class="post-img" role="img" aria-label="Couple walking together outdoors" style="background:linear-gradient(135deg,#d8dfc9,#98a57e)"></div><h3>Your Blog Title here</h3><p>Five listening habits that help your partner feel valued and understood.</p><a class="more">Read More</a></article>
      <article class="post"><div class="post-img" role="img" aria-label="Couple smiling at each other" style="background:linear-gradient(135deg,#e4d7cd,#b89f8d)"></div><h3>Your Blog Title here</h3><p>Planning time together so your relationship stays a priority each week.</p><a class="more">Read More</a></article>
      <article class="post"><div class="post-img" role="img" aria-label="Family relaxing at the beach" style="background:linear-gradient(135deg,#d6e8f0,#8fb6c8)"></div><h3>Your Blog Title here</h3><p>Balancing parenting and partnership without losing sight of each other.</p><a class="more">Read More</a></article>
    </div>
  </div>
</section>

<footer class="site-footer">
  <div class="wrap">
    <div class="footer-brand">
      <div class="brand">
        <span class="brand-dot"></span>
        <div>
          <div class="brand-name">The Kelvale Clinic</div>
          <div class="brand-tag">helping you create loving relationships</div>
        </div>
      </div>
    </div>
    <div class="foot-col">
      <h4>Quick Links</h4>
      <ul><li>Home</li><li>About Us</li><li>Our Blogs</li><li>Shop Cart</li><li>Contact Us</li></ul>
    </div>
    <div class="foot-col">
      <h4>Resources</h4>
      <ul><li>Counselling Types</li><li>Our Therapy</li><li>Quizzes</li><li>FAQ</li><li>Relationship Counselling</li></ul>
    </div>
    <div class="foot-col">
      <h4>Contact Us</h4>
      <ul><li>PO Box 210, Kelvale NSW 2000</li><li>1300 555 014</li><li>Email: hello@kelvale.example</li></ul>
      <div class="social"><span></span><span></span><span></span><span></span></div>
    </div>
  </div>
</footer>
<div class="bottom-bar">© 2017 The Kelvale Clinic. All rights reserved.</div>

</body>
</html>
```